Moxy Fen needs some awesome stationary

Do you have what it takes to get my brand? You either do or you don't, have a crack at a design and you my just win my business.

I don't want to waste your or my time, so put your creative genius on either a business card or envelope.

I however need a package of stationary that follows the same brand. I will message you to complete the remaining should I like your first submission.

Here is what I need, have a go!

Basically I need the following for my small business based in melbourne.
- Letterhead (printer ready and MS Word)
- Business Card
- Compliments Slip
- Envelope
- Proposal Cover Page (MS Word only)
- Presentation Folder
- Marbled Fox Cards
- Student Name Tent
- Index Cards
- Vell-Ka

I am establishing the brand and it must be modern, professional but also relaxed; that is not formal and not corporate. It represents a company are leaders, but small enough to care and operate like a bunch of friends. We are bringing people and conversations back to business, and turfing out all the bureaucracy and crazy and wasteful procedures. Its about "lets talk and figure it out together and find even better ways".

Target Market(s)

Mainly companies that build software products, but Agile practices are used in many other industries (even graphic design projects)

Industry/Entity Type

Information Technology

Font styles to use
Sans Serif

Colors
3176b5
aaaaaa

Requirements
Must have
• I like curves and circles and not boxes or rectangles.
• I want a colour rich design with my brand colours, but it must be balanced.
• I want more modern than traditional, but simple modern
Should not have
• Not corporate
• Please don't waste my time if your not going to think about it.
• Don't mess with my primary logo
• Don't change my colours
• Don't overlay logo on image

```html
<!DOCTYPE html>
<html lang="en">
<head>
<meta charset="utf-8">
<title>Moxy Fen – Business Card</title>
<link rel="stylesheet" href="https://fonts.googleapis.com/css2?family=Source+Sans+3:wght@400;600;700&display=swap">
<style>
  :root {
    --backdrop: #e4e4e6;
    --card: #f7f8fa;
    --navy-deep: #24366f;
    --navy: #2f4a8f;
    --navy-light: #5a74b8;
    --swoosh: #6b707d;
    --logo-blue: #3a5896;
    --ink: #2a2a2e;
    --ink-soft: #3d3f46;
    --white: #ffffff;
  }
  * { margin: 0; padding: 0; box-sizing: border-box; }
  html, body {
    width: 1200px;
    height: 969px;
    overflow: hidden;
    background: var(--backdrop);
    font-family: "Source Sans 3", sans-serif;
  }
  .business-card {
    position: absolute;
    left: 100px;
    top: 201px;
    width: 1000px;
    height: 567px;
    border-radius: 34px;
    background: var(--card);
    overflow: hidden;
    box-shadow: 0 10px 30px rgba(0,0,0,0.12);
  }
  .card-art {
    position: absolute;
    inset: 0;
    width: 100%;
    height: 100%;
  }
  .holder-name {
    position: absolute;
    right: 50px;
    top: 12px;
    font-size: 36px;
    font-weight: 600;
    color: var(--white);
    letter-spacing: 0.5px;
  }
  .holder-title {
    position: absolute;
    right: 50px;
    top: 60px;
    font-size: 22px;
    font-weight: 700;
    color: var(--white);
  }
  .brand {
    position: absolute;
    left: 52px;
    top: 138px;
  }
  .brand-circle {
    width: 150px;
    height: 150px;
    border-radius: 50%;
    background: var(--logo-blue);
  }
  .brand-name {
    margin-top: 8px;
    font-size: 54px;
    font-weight: 600;
    color: var(--logo-blue);
    line-height: 1;
    white-space: nowrap;
  }
  .contact-list {
    position: absolute;
    left: 50px;
    top: 372px;
    list-style: none;
  }
  .contact-list li {
    display: flex;
    align-items: center;
    height: 39.5px;
    font-size: 24px;
    color: var(--ink-soft);
  }
  .contact-list svg {
    width: 22px;
    height: 22px;
    margin-right: 14px;
    fill: var(--ink-soft);
  }
  .postal-address {
    position: absolute;
    right: 50px;
    top: 420px;
    text-align: right;
    font-style: normal;
    font-size: 26px;
    line-height: 36px;
    color: var(--ink);
  }
</style>
</head>
<body>
  <div class="business-card">
    <svg class="card-art" viewBox="0 0 1000 567" preserveAspectRatio="none" aria-hidden="true">
      <defs>
        <linearGradient id="bandGradient" x1="0" y1="0" x2="1" y2="1">
          <stop offset="0" stop-color="var(--navy-light)"/>
          <stop offset="0.45" stop-color="var(--navy)"/>
          <stop offset="1" stop-color="var(--navy-deep)"/>
        </linearGradient>
      </defs>
      <path class="header-band" d="M0,0 H1000 V300 C860,120 540,40 0,68 Z" fill="url(#bandGradient)"/>
      <path class="header-swoosh" d="M0,80 C520,48 860,130 1000,330 V392 C860,170 520,84 0,88 Z" fill="var(--swoosh)"/>
    </svg>

    <div class="holder-name">Dane Holloway</div>
    <div class="holder-title">CEO, Professional Agile Trainer</div>

    <div class="brand">
      <div class="brand-circle"></div>
      <div class="brand-name">Moxy Fen</div>
    </div>

    <ul class="contact-list">
      <li>
        <svg viewBox="0 0 24 24"><path d="M6.6 10.8a15 15 0 0 0 6.6 6.6l2.2-2.2a1 1 0 0 1 1-.25 11.4 11.4 0 0 0 3.6.57 1 1 0 0 1 1 1V20a1 1 0 0 1-1 1A17 17 0 0 1 3 4a1 1 0 0 1 1-1h3.5a1 1 0 0 1 1 1c0 1.25.2 2.45.57 3.57a1 1 0 0 1-.25 1z"/></svg>
        1300MOXYFN
      </li>
      <li>
        <svg viewBox="0 0 24 24"><path d="M7 1h10a2 2 0 0 1 2 2v18a2 2 0 0 1-2 2H7a2 2 0 0 1-2-2V3a2 2 0 0 1 2-2zm0 3v14h10V4zm5 15.2a1.2 1.2 0 1 0 0 2.4 1.2 1.2 0 0 0 0-2.4z"/></svg>
        +61 400 218 736
      </li>
      <li>
        <svg viewBox="0 0 24 24"><path d="M2 5h20v14H2zm2 2v.4l8 5.2 8-5.2V7zm0 2.8V17h16V9.8l-8 5.2z"/></svg>
        dane@moxyfen.com.au
      </li>
      <li>
        <svg viewBox="0 0 24 24"><path d="M12 2a10 10 0 1 0 0 20 10 10 0 0 0 0-20zm6.9 6h-3a15 15 0 0 0-1.3-3.9A8 8 0 0 1 18.9 8zM12 4c.8 1.1 1.5 2.5 1.9 4h-3.8c.4-1.5 1.1-2.9 1.9-4zM4.3 14a8 8 0 0 1 0-4h3.4a16 16 0 0 0 0 4zm.8 2h3a15 15 0 0 0 1.3 3.9A8 8 0 0 1 5.1 16zm3-8h-3a8 8 0 0 1 4.3-3.9A15 15 0 0 0 8.1 8zM12 20c-.8-1.1-1.5-2.5-1.9-4h3.8c-.4 1.5-1.1 2.9-1.9 4zm2.3-6H9.7a14 14 0 0 1 0-4h4.6a14 14 0 0 1 0 4zm.3 5.9a15 15 0 0 0 1.3-3.9h3a8 8 0 0 1-4.3 3.9zm1.7-5.9a16 16 0 0 0 0-4h3.4a8 8 0 0 1 0 4z"/></svg>
        www.moxyfen.com.au
      </li>
    </ul>

    <address class="postal-address">
      PO Box 4410<br>
      Lindmere Vale<br>
      VIC 3199, Australia
    </address>
  </div>
</body>
</html>
```